Design and Renovation Company Luxury Business Card

I want to create a luxury business card for a Design and Renovation Firm . We will use our current logo. The company name is 528BUILDA. We do not want anything standard. We need a very unique concept.
Please see uploaded inspiration. I really like the textured paper option. I would like the card to be thick with debossing, and/or embossing options. The logo has orange in it but I would like to see the card with and without the orange. I think the orange may make the company feel less high-end. The goal is to elevate the logo not match its vibe per se of the logo. We want something very unique, not standard at all!
I would like a space for :
Logo,
Name,
Position,
Email,
Office number,
Website Address,
Business Address,
Thank you!
Have fun!
Target Market(s)
Home owners Age 35 +
Industry/Entity Type
Design and Renovation
Contact Information for Business Card
Logo, Name, Position, Email, Office number, Website Address, Business Address,.
Colors
Designer to choose colors to be used in the design.
Requirements
Must have
- A luxury designer feel. Must be black or dark grey but open to other luxury ideas.
Nice to have
- Gold, silver, black embossing or debossing. Textured paper design.
Should not have
- A cheap look and feel.

```html
<!DOCTYPE html>
<html lang="en">
<head>
<meta charset="utf-8">
<title>528BUILDA Business Card</title>
<link rel="stylesheet" href="https://fonts.googleapis.com/css2?family=Poppins:wght@400;500;600&display=swap">
<style>
  :root {
    --page-bg: #dfe3e4;
    --card-bg: #222326;
    --text-light: #f4f4f4;
    --brand-tone: #7d7e82;
  }
  * { margin: 0; padding: 0; box-sizing: border-box; }
  html, body {
    width: 1200px; height: 960px; overflow: hidden;
    background: var(--page-bg);
    font-family: "Poppins", sans-serif;
  }
  .card {
    position: absolute;
    left: 250px;
    width: 701px; height: 400px;
    background: var(--card-bg);
    overflow: hidden;
  }
  .card--front { top: 60px; }
  .card--back { top: 500px; }

  .front-pattern {
    position: absolute; inset: 0;
    background:
      linear-gradient(200deg, rgba(233,233,234,0.92) 0%, rgba(200,200,202,0.55) 22%, rgba(60,61,64,0.2) 45%, rgba(0,0,0,0) 60%),
      linear-gradient(180deg, #262729 0%, #1b1c1e 100%);
  }

  .name-bar {
    position: absolute; left: 0; top: 153px;
    width: 19px; height: 47px;
    background: var(--text-light);
  }
  .person-name {
    position: absolute; left: 25px; top: 152px;
    font-size: 33px; line-height: 1; font-weight: 400;
    color: var(--text-light); letter-spacing: 0.3px;
  }
  .person-name strong { font-weight: 600; }
  .person-role {
    position: absolute; left: 26px; top: 184px;
    font-size: 16.5px; font-weight: 500; color: var(--text-light);
  }
  .address {
    position: absolute; left: 26px; top: 227px;
    font-size: 17px; line-height: 24.5px; font-weight: 400;
    color: var(--text-light); letter-spacing: 0.4px;
  }
  .contact-list {
    position: absolute; left: 26px; top: 301px;
    list-style: none;
  }
  .contact-list li {
    display: flex; align-items: center;
    height: 24.5px;
    font-size: 17px; color: var(--text-light); letter-spacing: 0.4px;
  }
  .contact-list svg { width: 16px; height: 16px; margin-right: 14px; flex: none; }

  .brand {
    position: absolute; right: 34px; top: 30px;
    text-align: right;
  }
  .brand-name {
    display: block;
    font-size: 22px; font-weight: 600; line-height: 1.1;
    color: var(--brand-tone); letter-spacing: 2px;
  }
  .brand-tagline {
    display: block; margin-top: 4px;
    font-size: 11px; font-weight: 500;
    color: var(--brand-tone); letter-spacing: 1.6px;
  }
</style>
</head>
<body>
  <section class="card card--front">
    <div class="front-pattern" role="img" aria-label="Decorative grid of small square tiles fading from bright white at the top right to deep black at the bottom left"></div>
  </section>

  <section class="card card--back">
    <div class="brand">
      <span class="brand-name">528BUILDA</span>
      <span class="brand-tagline">Design and Renovation Firm</span>
    </div>
    <div class="name-bar"></div>
    <h1 class="person-name"><strong>Marta</strong> Kolarova</h1>
    <p class="person-role">Founder &amp; CEO</p>
    <p class="address">1840 Alder Grove Rd. Suite 310<br>Lakeview, TX 75001</p>
    <ul class="contact-list">
      <li>
        <svg viewBox="0 0 24 24" aria-hidden="true"><path fill="#f4f4f4" d="M6.6 10.8a15 15 0 0 0 6.6 6.6l2.2-2.2a1 1 0 0 1 1-.25 11.4 11.4 0 0 0 3.6.57 1 1 0 0 1 1 1V20a1 1 0 0 1-1 1A17 17 0 0 1 3 4a1 1 0 0 1 1-1h3.5a1 1 0 0 1 1 1c0 1.25.2 2.45.57 3.57a1 1 0 0 1-.25 1z"/></svg>
        (555) 014-2290
      </li>
      <li>
        <svg viewBox="0 0 24 24" aria-hidden="true"><rect x="2" y="5" width="20" height="14" rx="1.5" fill="#f4f4f4"/><path d="M3 6.5l9 6.5 9-6.5" fill="none" stroke="#222326" stroke-width="1.8"/></svg>
        info@yourwebsite.com
      </li>
      <li>
        <svg viewBox="0 0 24 24" aria-hidden="true"><g fill="none" stroke="#f4f4f4" stroke-width="1.8"><circle cx="12" cy="12" r="9.5"/><ellipse cx="12" cy="12" rx="4" ry="9.5"/><path d="M2.5 12h19M4 7h16M4 17h16"/></g></svg>
        www.yourwebsite.com
      </li>
    </ul>
  </section>
</body>
</html>
```